Swing Dance Themed Cleaning Company Website

We need a website designed for a cleaning company based in Portland, Oregon called Foxtrot Lane. We clean homes and commercial buildings, inside and out.

needs to be vintage and like the velvet tambour. Speakeasy 1920s feel.
needs to be classy.

Check out foxtrotlane.com We are not happy with the site currently.

please look at house scout site for more content https://www.housescoutpro.com/rated.FoxtrotLaneCleaning.48217705.html

Check out my videos on my ClipHaven channel Foxtrot Lane

Target Market(s)

middle class and home owner

Industry/Entity Type

Cleaning Service

Number of Pages Required

3 page

Font styles to use
Other font styles liked:
• jazzrag

Colors

Designer to choose colors to be used in the design.

Requirements
Must have
• must be good on pc and mobile

```html
<!DOCTYPE html>
<html lang="en">
<head>
<meta charset="utf-8">
<title>Foxtrot Lane – Sweep Portland In Style</title>
<link href="https://fonts.googleapis.com/css2?family=Lato:ital,wght@0,400;0,700;0,900;1,400&family=Poiret+One&display=swap" rel="stylesheet">
<style>
:root{
  --gold:#f2b705;
  --gold-deep:#e0a100;
  --ink:#111111;
  --charcoal:#2b2b2b;
  --grey:#6d6d6d;
  --mist:#f1f1f1;
  --white:#ffffff;
  --line:#dddddd;
}
*{box-sizing:border-box;margin:0;padding:0}
html,body{width:1200px;height:3830px;overflow:hidden}
body{font-family:'Lato',sans-serif;color:var(--ink);background:var(--white);position:relative}
.deco{font-family:'Poiret One',sans-serif;font-weight:400}
.abs{position:absolute}

/* header */
.site-header{position:absolute;left:0;top:0;width:1200px;height:145px;background:var(--white)}
.brand{position:absolute;left:77px;top:30px;display:flex;align-items:center;gap:14px}
.brand-mark{width:40px;height:40px;background:var(--gold);border-radius:50%}
.brand-name{font-weight:900;font-size:34px;line-height:1;color:var(--ink);letter-spacing:1px}
.brand-tag{position:absolute;left:77px;top:100px;font-size:12px;font-weight:700;letter-spacing:.5px}
.call{position:absolute;left:893px;top:40px;display:flex;gap:18px;align-items:center}
.call small{display:block;font-size:14px;color:var(--grey)}
.call strong{display:block;font-size:26px;font-weight:400;margin-top:6px}

.nav{position:absolute;left:0;top:145px;width:1200px;height:75px;background:var(--ink)}
.nav-gold{position:absolute;left:0;top:0;width:843px;height:75px;background:var(--gold)}
.nav ul{list-style:none;position:absolute;left:80px;top:0;display:flex;gap:48px;height:75px;align-items:center}
.nav li{color:var(--white);font-size:17px;font-weight:400}
.nav-search{position:absolute;left:750px;top:17px;width:42px;height:42px;border-radius:50%;background:var(--gold-deep)}
.nav-cta{position:absolute;left:880px;top:0;line-height:75px;color:var(--white);font-size:18px;letter-spacing:.5px}

/* hero */
.hero{position:absolute;left:0;top:220px;width:1200px;height:572px;background:linear-gradient(100deg,#6b7368 0%,#9ea39a 35%,#b3aca4 60%,#8f7f76 100%)}
.hero::after{content:"";position:absolute;inset:0;background:rgba(0,0,0,.25)}
.hero-copy{position:absolute;left:0;top:150px;width:1200px;text-align:center;z-index:2;color:var(--white)}
.hero-copy h1{font-size:35px;font-weight:900;line-height:1.45;letter-spacing:1px}
.hero-copy p{font-size:14px;line-height:1.6;width:580px;margin:18px auto 0}
.btn{display:inline-block;background:var(--gold);color:var(--white);font-size:16px;letter-spacing:.5px;padding:0 28px;line-height:60px}
.hero-copy .btn{margin-top:40px}
.slider-arrow{position:absolute;top:260px;width:62px;height:62px;border-radius:50%;z-index:2;display:flex;align-items:center;justify-content:center}

/* why choose */
.section-title{position:absolute;left:0;width:1200px;text-align:center;font-size:38px;letter-spacing:2px;color:var(--ink)}
.feature{position:absolute;top:940px;width:242px;height:230px;border-radius:30px 0 30px 0;background:var(--white);box-shadow:0 4px 14px rgba(0,0,0,.12);text-align:center}
.feature.is-active{background:linear-gradient(160deg,#f7c516,var(--gold-deep))}
.feature .icon{width:92px;height:92px;border-radius:50%;background:var(--gold);margin:30px auto 0;display:flex;align-items:center;justify-content:center}
.feature.is-active .icon{background:var(--white)}
.feature h3{font-weight:400;font-size:19px;margin-top:28px;line-height:1.3}

/* about */
.about{position:absolute;left:0;top:1233px;width:1200px;height:427px;background:linear-gradient(90deg,#f3f2ef 0%,#e9e6e0 40%,#d8d3cb 100%)}
.about-copy{position:absolute;left:77px;top:60px;width:560px}
.about-copy h2{font-size:38px;color:var(--gold-deep);letter-spacing:1px}
.about-copy .lead{font-size:14px;font-style:italic;color:var(--grey);margin-top:18px}
.about-copy h3{font-size:24px;font-weight:400;margin-top:22px}
.about-copy p{font-size:14px;color:var(--grey);line-height:1.7;margin-top:18px;width:560px}
.about-copy .btn{margin-top:32px}
.about-video{position:absolute;left:684px;top:61px;width:439px;height:291px;background:linear-gradient(135deg,#56647a,#8a94a4 50%,#3d4656)}
.play{position:absolute;left:188px;top:114px;width:64px;height:64px;border-radius:50%;border:3px solid var(--gold);display:flex;align-items:center;justify-content:center}

/* services */
.service{position:absolute;top:1795px;width:250px;height:332px;background:var(--white);box-shadow:0 3px 12px rgba(0,0,0,.14);text-align:center}
.service .photo{margin:12px 12px 0;height:155px}
.service h3{font-size:24px;color:var(--gold-deep);font-weight:400;margin-top:22px}
.service p{font-size:13px;line-height:1.7;color:var(--grey);margin:12px 22px 0}

/* reviews */
.reviews{position:absolute;left:0;top:2200px;width:1200px;height:500px;background:linear-gradient(90deg,#2e2e2e,#4a4643 50%,#2b2b2b)}
.reviews h2{position:absolute;left:80px;top:60px;font-size:33px;color:var(--white);letter-spacing:1px;white-space:nowrap}
.reviews .rule{position:absolute;left:420px;top:82px;width:590px;height:1px;background:rgba(255,255,255,.5)}
.r-arrow{position:absolute;top:62px;width:46px;height:46px;border-radius:50%;display:flex;align-items:center;justify-content:center}
.review{position:absolute;top:158px;width:320px;color:var(--white)}
.avatar{width:100px;height:100px;border-radius:50%;border:4px solid var(--gold);background:linear-gradient(135deg,#d9dde2,#a9b3bd)}
.review .who{position:absolute;left:125px;top:14px}
.review .who strong{font-size:15px;font-weight:700;display:block}
.review .who small{font-size:12px;opacity:.8;display:block;margin-top:8px}
.stars{margin-top:10px;display:flex;gap:3px}
.review p{font-size:16px;font-style:italic;line-height:2.25;margin-top:26px}
.review p .q{font-size:50px;font-style:normal;font-weight:900;line-height:0;vertical-align:-14px;margin-right:10px}

/* promo */
.promo-art{position:absolute;left:100px;top:2718px;width:410px;height:470px;background:radial-gradient(ellipse at 50% 50%,#d6d6d6 0%,#f2f2f2 60%,#ffffff 75%)}
.promo-card{position:absolute;left:460px;top:2821px;width:587px;height:307px;border-radius:80px 0 80px 0;background:linear-gradient(160deg,#f8c919,var(--gold-deep))}
.promo-card p{position:absolute;left:73px;top:95px;width:340px;text-align:center;font-size:23px;line-height:1.5;color:var(--ink)}
.promo-pill{position:absolute;left:597px;top:3043px;width:440px;height:67px;border-radius:34px;background:var(--ink);color:var(--white)}
.promo-pill strong{position:absolute;left:60px;top:12px;font-size:33px;font-weight:900}
.promo-pill span{position:absolute;left:265px;top:25px;font-size:13px;font-weight:900;text-decoration:underline}

/* achievements */
.achieve{position:absolute;left:0;top:3242px;width:1200px;height:123px;background:var(--mist)}
.achieve-band{position:absolute;left:0;top:0;width:567px;height:123px}
.achieve h2{position:absolute;left:80px;top:25px;font-size:33px;color:var(--white);letter-spacing:1px}
.achieve p{position:absolute;left:80px;top:80px;font-size:13px;color:var(--white)}
.badge{position:absolute;top:18px;width:86px;height:86px}

/* footer */
.footer{position:absolute;left:0;top:3365px;width:1200px;height:388px;background:var(--ink);color:var(--white)}
.footer h4{position:absolute;top:65px;font-family:'Poiret One',sans-serif;font-weight:400;font-size:20px;letter-spacing:1px}
.f-item{position:absolute;font-size:14px;line-height:1.8}
.nav-list{list-style:none;position:absolute;left:347px;top:118px;font-size:14px;line-height:2.1}
.post{position:absolute;left:533px;width:260px;height:84px}
.post .thumb{position:absolute;left:0;top:0;width:84px;height:84px;background:linear-gradient(135deg,#c7ccd3,#8b98a6)}
.post small{position:absolute;left:98px;top:0;font-size:12px;font-style:italic}
.post span{position:absolute;left:98px;top:28px;font-size:14px;line-height:1.7}
.newsletter p{position:absolute;left:872px;top:118px;width:255px;font-size:13px;line-height:1.8}
.news-form{position:absolute;left:872px;top:210px;width:250px;height:46px;background:var(--white);border-radius:23px}
.news-form span{position:absolute;left:18px;top:14px;font-size:13px;color:var(--grey)}
.news-form i{position:absolute;right:0;top:0;width:64px;height:46px;border-radius:23px;background:var(--gold);display:flex;align-items:center;justify-content:center}
.legal{position:absolute;left:0;top:3753px;width:1200px;height:77px;background:var(--gold)}
.legal p{position:absolute;left:80px;top:30px;font-size:13px;color:var(--ink)}
.social{position:absolute;top:20px;width:36px;height:36px;border-radius:50%;background:var(--ink)}
</style>
</head>
<body>

<header class="site-header">
  <div class="brand"><span class="brand-mark"></span><span class="brand-name">FOXTROT LANE</span></div>
  <div class="brand-tag">SWEEP PORTLAND IN STYLE</div>
  <div class="call">
    <svg width="56" height="56" viewBox="0 0 24 24"><path fill="#f2b705" d="M6.6 10.8a15 15 0 0 0 6.6 6.6l2.2-2.2c.3-.3.7-.4 1-.2 1.1.4 2.3.6 3.6.6.6 0 1 .4 1 1V20c0 .6-.4 1-1 1A17 17 0 0 1 3 4c0-.6.4-1 1-1h3.5c.6 0 1 .4 1 1 0 1.3.2 2.5.6 3.6.1.3 0 .7-.2 1z"/></svg>
    <div><small>Call Us Now</small><strong>123-456-7890</strong></div>
  </div>
</header>

<nav class="nav">
  <div class="nav-gold"></div>
  <ul><li>HOME</li><li>ABOUT US</li><li>OUR SERVICES</li><li>BLOG</li><li>CONTACT</li></ul>
  <div class="nav-search"><svg width="42" height="42" viewBox="0 0 42 42"><circle cx="19" cy="19" r="7" fill="none" stroke="#111" stroke-width="2.5"/><line x1="24" y1="24" x2="29" y2="29" stroke="#111" stroke-width="2.5"/></svg></div>
  <div class="nav-cta">BOOK AN APPOINTMENT</div>
</nav>

<section class="hero" role="img" aria-label="Photo of a cleaner in yellow gloves spraying and wiping a table beside potted flowers">
  <div class="slider-arrow" style="left:45px;background:#fff"><svg width="20" height="20" viewBox="0 0 20 20"><path d="M12 4 6 10l6 6" fill="none" stroke="#111" stroke-width="2.5"/></svg></div>
  <div class="slider-arrow" style="left:1093px;background:var(--gold)"><svg width="20" height="20" viewBox="0 0 20 20"><path d="m8 4 6 6-6 6" fill="none" stroke="#fff" stroke-width="2.5"/></svg></div>
  <div class="hero-copy">
    <h1>WE KEEP YOUR WORLD FRESH AND<br>SPARKLING CLEAN</h1>
    <p>Lorem Ipsum is simply dummy text of the printing and typesetting industry. Lorem Ipsum has been the industry's standard dummy text ever since the 1500s.</p>
    <span class="btn">LEARN MORE</span>
  </div>
</section>

<h2 class="section-title deco" style="top:848px">WHY CHOOSE US...?</h2>
<div class="feature is-active" style="left:77px"><div class="icon"><svg width="44" height="44" viewBox="0 0 24 24"><path d="M4 21V9l8-6 8 6v12h-5v-6H9v6z" fill="#111"/></svg></div><h3>Cleaning &amp; Maid<br>Services</h3></div>
<div class="feature" style="left:345px"><div class="icon"><svg width="44" height="44" viewBox="0 0 24 24"><path d="M5 20h14l-2-8H7zM11 4h2v8h-2z" fill="#111"/></svg></div><h3>Janitorial</h3></div>
<div class="feature" style="left:613px"><div class="icon"><svg width="44" height="44" viewBox="0 0 24 24"><path d="M3 20h18v-2H3zM14 4h2v12h-2zM10 16h10v2H10z" fill="#111"/></svg></div><h3>Carpet Cleaning</h3></div>
<div class="feature" style="left:881px"><div class="icon"><svg width="44" height="44" viewBox="0 0 24 24"><rect x="5" y="4" width="14" height="16" fill="none" stroke="#111" stroke-width="2"/><line x1="12" y1="4" x2="12" y2="20" stroke="#111" stroke-width="2"/><line x1="5" y1="12" x2="19" y2="12" stroke="#111" stroke-width="2"/></svg></div><h3>Window Washing</h3></div>

<section class="about">
  <div class="about-copy">
    <h2 class="deco">ABOUT US</h2>
    <div class="lead">Making the greater Portland area clean, one building at a time</div>
    <h3>Good people, great service</h3>
    <p>Foxtrot Lane is a family owned professional cleaning business. We provide our years of cleaning experience to homes and businesses in and around Portland, Oregon.</p>
    <span class="btn">LEARN MORE</span>
  </div>
  <div class="about-video" role="img" aria-label="Video still of a smiling cleaner holding a mop and supplies">
    <div class="play"><svg width="26" height="26" viewBox="0 0 26 26"><path d="M8 5v16l13-8z" fill="#f2b705"/></svg></div>
  </div>
</section>

<h2 class="section-title deco" style="top:1715px">OUR SERVICES</h2>
<div class="service" style="left:77px"><div class="photo" role="img" aria-label="Photo of a janitorial team cleaning an office" style="background:linear-gradient(135deg,#b9d3e3,#6f9fbf)"></div><h3>Janitorial Services</h3><p>Routine janitorial, Tall cleaning, Food service sanitation, Clean room services</p></div>
<div class="service" style="left:347px"><div class="photo" role="img" aria-label="Photo of house cleaners tidying a living room" style="background:linear-gradient(135deg,#e8c9a4,#b9865a)"></div><h3>House-cleaning</h3><p>Floors, Carpet cleaning, Refuse removal, Dusting, Interior windows, Blinds</p></div>
<div class="service" style="left:617px"><div class="photo" role="img" aria-label="Photo of a maintenance cleaner with a supply basket" style="background:linear-gradient(135deg,#efe4d8,#b8a898)"></div><h3>Maintenance</h3><p>Pressure washing, Gutters, Painting, Exterior windows, Construction cleanup, Detailing</p></div>
<div class="service" style="left:887px"><div class="photo" role="img" aria-label="Photo of a crew cleaning up after an event" style="background:linear-gradient(135deg,#c9d4de,#7e8fa0)"></div><h3>Event services</h3><p>Event hosting at the birch hall loft Event cleanup</p></div>

<section class="reviews" role="region" aria-label="Customer reviews">
  <h2 class="deco">CUSTOMER REVIEW</h2>
  <div class="rule"></div>
  <div class="r-arrow" style="left:1022px;background:var(--gold)"><svg width="16" height="16" viewBox="0 0 16 16"><path d="M10 3 5 8l5 5" fill="none" stroke="#fff" stroke-width="2.5"/></svg></div>
  <div class="r-arrow" style="left:1073px;background:#fff"><svg width="16" height="16" viewBox="0 0 16 16"><path d="m6 3 5 5-5 5" fill="none" stroke="#111" stroke-width="2.5"/></svg></div>

  <div class="review" style="left:80px"><div class="avatar" role="img" aria-label="Customer portrait"></div><div class="who"><strong>MARLA QUINCE</strong><small>Genuine Customer</small><div class="stars"><svg width="80" height="14" viewBox="0 0 80 14"><g fill="#f2b705"><path id="s" d="M7 0l2 5h5l-4 3 2 5-5-3-5 3 2-5-4-3h5z"/><use href="#s" x="16"/><use href="#s" x="32"/><use href="#s" x="48"/></g><use href="#s" x="64" fill="none" stroke="#f2b705"/></svg></div></div><p><span class="q">“</span>Lorem Ipsum is simply dummy text of the printing and typesetting industry. Lorem Ipsum has been the industry's</p></div>
  <div class="review" style="left:445px"><div class="avatar" role="img" aria-label="Customer portrait"></div><div class="who"><strong>MARLA QUINCE</strong><small>Genuine Customer</small><div class="stars"><svg width="80" height="14" viewBox="0 0 80 14"><g fill="#f2b705"><use href="#s"/><use href="#s" x="16"/><use href="#s" x="32"/><use href="#s" x="48"/></g><use href="#s" x="64" fill="none" stroke="#f2b705"/></svg></div></div><p><span class="q">“</span>Lorem Ipsum is simply dummy text of the printing and typesetting industry. Lorem Ipsum has been the industry's</p></div>
  <div class="review" style="left:810px"><div class="avatar" role="img" aria-label="Customer portrait"></div><div class="who"><strong>MARLA QUINCE</strong><small>Genuine Customer</small><div class="stars"><svg width="80" height="14" viewBox="0 0 80 14"><g fill="#f2b705"><use href="#s"/><use href="#s" x="16"/><use href="#s" x="32"/><use href="#s" x="48"/></g><use href="#s" x="64" fill="none" stroke="#f2b705"/></svg></div></div><p><span class="q">“</span>Lorem Ipsum is simply dummy text of the printing and typesetting industry. Lorem Ipsum has been the industry's</p></div>
</section>

<div class="promo-art" role="img" aria-label="Vintage ink illustration of a dapper 1920s gentleman dancing with a mop"></div>
<div class="promo-card"><p>Save 95% on first hour of House Cleaning Services for First Time Customers</p></div>
<div class="promo-pill"><strong>Save 95 %</strong><span>LEARN MORE</span></div>

<section class="achieve">
  <svg class="achieve-band" viewBox="0 0 567 123" preserveAspectRatio="none"><polygon points="0,0 520,0 567,61 520,123 0,123" fill="#f2b705"/></svg>
  <h2 class="deco">OUR ACHIEVEMENTS</h2>
  <p>Lorem Ipsum is simply dummy text printing and typesetting industry.</p>
  <svg class="badge" style="left:620px" viewBox="0 0 86 86" aria-label="Award badge"><rect x="13" y="6" width="60" height="74" rx="6" fill="#8a96a3"/></svg>
  <svg class="badge" style="left:758px" viewBox="0 0 86 86" aria-label="Award badge"><polygon points="43,4 80,22 80,64 43,82 6,64 6,22" fill="#5a6b7c"/></svg>
  <svg class="badge" style="left:896px" viewBox="0 0 86 86" aria-label="Award badge"><polygon points="10,6 76,6 76,62 43,82 10,62" fill="#7b8894"/></svg>
  <svg class="badge" style="left:1034px" viewBox="0 0 86 86" aria-label="Award badge"><circle cx="43" cy="43" r="38" fill="#9aa5b0"/></svg>
</section>

<footer class="footer">
  <h4 style="left:80px">GET IN TOUCH</h4>
  <svg class="abs" style="left:80px;top:120px" width="16" height="20" viewBox="0 0 16 20"><path d="M8 0a7 7 0 0 0-7 7c0 5 7 13 7 13s7-8 7-13a7 7 0 0 0-7-7zm0 10a3 3 0 1 1 0-6 3 3 0 0 1 0 6z" fill="#f2b705"/></svg>
  <div class="f-item" style="left:112px;top:113px">418 SE Birch St #210,<br>Portland, OR 97215</div>
  <svg class="abs" style="left:80px;top:192px" width="16" height="16" viewBox="0 0 24 24"><path fill="#f2b705" d="M6.6 10.8a15 15 0 0 0 6.6 6.6l2.2-2.2c.3-.3.7-.4 1-.2 1.1.4 2.3.6 3.6.6.6 0 1 .4 1 1V20c0 .6-.4 1-1 1A17 17 0 0 1 3 4c0-.6.4-1 1-1h3.5c.6 0 1 .4 1 1 0 1.3.2 2.5.6 3.6.1.3 0 .7-.2 1z"/></svg>
  <div class="f-item" style="left:112px;top:186px">971-555-0148</div>
  <svg class="abs" style="left:80px;top:252px" width="16" height="12" viewBox="0 0 16 12"><rect width="16" height="12" fill="#f2b705"/><path d="M0 0l8 6 8-6" fill="none" stroke="#111" stroke-width="1.5"/></svg>
  <div class="f-item" style="left:112px;top:244px">nora@foxtrotlane.com</div>

  <h4 style="left:347px">NAVIGATION</h4>
  <ul class="nav-list"><li>Home</li><li>About Us</li><li>Our Services</li><li>Blog</li><li>Contact</li></ul>

  <h4 style="left:533px">RECENT BLOG</h4>
  <div class="post" style="top:118px"><div class="thumb" role="img" aria-label="Blog thumbnail of cleaners at work"></div><small>Posted at 26/07/2018</small><span>Lorem Ipsum is simply<br>Ipsum is simply dummy</span></div>
  <div class="post" style="top:226px"><div class="thumb" role="img" aria-label="Blog thumbnail of cleaners at work"></div><small>Posted at 26/07/2018</small><span>Lorem Ipsum is simply<br>Ipsum is simply dummy</span></div>

  <h4 style="left:872px">NEWSLETTER</h4>
  <div class="newsletter"><p>Lorem Ipsum is simply dummy text of the printing and typesetting industry. Lorem Ipsum has been the industry's.</p></div>
  <div class="news-form"><span>Email</span><i><svg width="20" height="20" viewBox="0 0 20 20"><path d="M2 10 18 2l-4 16-4-6z" fill="#fff"/></svg></i></div>
</footer>

<div class="legal">
  <p>Copyright © 2018 <strong>FOXTROT LANE.</strong></p>
  <span class="social" style="left:905px"></span>
  <span class="social" style="left:947px"></span>
  <span class="social" style="left:989px"></span>
  <span class="social" style="left:1031px"></span>
  <span class="social" style="left:1073px"></span>
</div>

</body>
</html>
```